Stylish Business Cards Wanted

- DOUBLE SIDED Design Required -

High end, edgy cards for a corporate and personal stylist. Must include logo,
Name: Belinda Harwick
Title: Director and Stylist
telephone : +61 8 7142 5809
email: belinda@theloombriefing.example
website: theloombriefing.example
Tag: Corporate Workwear & Uniform Specialist | Personal Stylist
Would like nice icons for telephone, email, website

Target Market(s)

Businesses wanting stylish uniforms, people wanting stylish wardrobes

Industry/Entity Type

Corporate Workwear Stylist

Contact Information for Business Card

I would like black, white and gold foiling incorporated in the design - possibly a touch of the other colours on my branding guide attached Name: Belinda Harwick Title: Director and Stylist telephone : +61 8 7142 5809 email: belinda@theloombriefing.example website: theloombriefing.example Tag: Corporate Workwear & Uniform Specialist | Personal Stylist Would like nice icons for telephone, email, website

Font styles to use
Other font styles liked:
• Raleway

Colors

Designer to choose colors to be used in the design.

Requirements
Must have
• Gold foil accents

```html
<!DOCTYPE html>
<html lang="en">
<head>
<meta charset="utf-8">
<title>The Loom Briefing – Business Cards</title>
<link href="https://fonts.googleapis.com/css2?family=Raleway:wght@400;500;600&family=Arimo:wght@400&display=swap" rel="stylesheet">
<style>
  :root {
    --backdrop: #dcdcdc;
    --ink: #0b0b0b;
    --paper: #ffffff;
    --gold: #e9bd55;
    --gold-soft: #f0cf7a;
    --text: #1a1a1a;
  }
  * { box-sizing: border-box; margin: 0; padding: 0; }
  html, body {
    width: 1200px; height: 900px; overflow: hidden;
    background: var(--backdrop);
    font-family: "Raleway", sans-serif;
  }
  .canvas {
    width: 1200px; height: 900px;
    display: flex; flex-direction: column; align-items: center; justify-content: center;
    gap: 44px;
  }
  .card {
    position: relative;
    width: 630px; height: 360px;
    box-shadow: 0 6px 14px rgba(0,0,0,0.18);
    border-bottom: 5px solid var(--gold);
    overflow: hidden;
  }
  /* Front */
  .card--front { background: var(--ink); display: flex; align-items: center; justify-content: center; }
  .brand-name {
    font-weight: 600; letter-spacing: 0.02em; line-height: 1;
  }
  .card--front .brand-name { color: var(--gold); font-size: 50px; }

  /* Back */
  .card--back { background: var(--paper); }
  .brand-block {
    position: absolute; left: 38px; top: 40px; width: 240px; height: 210px;
    display: flex; align-items: center; justify-content: center; text-align: center;
  }
  .card--back .brand-name { color: var(--ink); font-size: 38px; line-height: 1.1; }
  .divider {
    position: absolute; left: 302px; top: 58px; width: 2px; height: 178px;
    background: var(--gold);
  }
  .contact {
    position: absolute; left: 334px; top: 68px; right: 20px;
  }
  .contact__name { font-size: 25px; font-weight: 600; color: var(--text); letter-spacing: 0.01em; }
  .contact__title { font-size: 13px; color: var(--gold); margin-top: 1px; }
  .contact__list { list-style: none; margin-top: 30px; }
  .contact__item {
    display: flex; align-items: center; gap: 14px;
    font-family: "Arimo", sans-serif; font-size: 13.5px; color: var(--text);
    margin-bottom: 9px;
  }
  .contact__icon { width: 20px; height: 20px; flex: none; }
  .tagline-band {
    position: absolute; left: 0; right: 0; top: 284px; height: 48px;
    background: var(--ink);
    display: flex; align-items: center; justify-content: center; gap: 12px;
    color: var(--gold); font-size: 17px; font-weight: 500; letter-spacing: 0.01em;
    border-bottom: 4px solid var(--gold);
  }
  .tagline-band .sep { color: var(--paper); font-weight: 400; }
</style>
</head>
<body>
<main class="canvas">
  <section class="card card--front" aria-label="Card front">
    <span class="brand-name">The Loom Briefing</span>
  </section>

  <section class="card card--back" aria-label="Card back">
    <div class="brand-block"><span class="brand-name">The Loom<br>Briefing</span></div>
    <div class="divider"></div>
    <div class="contact">
      <p class="contact__name">Belinda Harwick</p>
      <p class="contact__title">Director and Stylist</p>
      <ul class="contact__list">
        <li class="contact__item">
          <svg class="contact__icon" viewBox="0 0 20 20" aria-hidden="true">
            <circle cx="10" cy="10" r="10" fill="#0b0b0b"/>
            <path d="M6.5 5.5l2 0 .8 2.3-1.2.9a6 6 0 0 0 2.7 2.7l.9-1.2 2.3.8 0 2a1 1 0 0 1-1 1A8 8 0 0 1 5.5 6.5a1 1 0 0 1 1-1z" fill="#e9bd55"/>
          </svg>
          +61 8 7142 5809
        </li>
        <li class="contact__item">
          <svg class="contact__icon" viewBox="0 0 20 20" aria-hidden="true">
            <circle cx="10" cy="10" r="10" fill="#0b0b0b"/>
            <rect x="5" y="6.5" width="10" height="7" rx="0.8" fill="#e9bd55"/>
            <path d="M5.3 7l4.7 3.6L14.7 7" fill="none" stroke="#0b0b0b" stroke-width="1"/>
          </svg>
          belinda@theloombriefing.example
        </li>
        <li class="contact__item">
          <svg class="contact__icon" viewBox="0 0 20 20" aria-hidden="true">
            <circle cx="10" cy="10" r="10" fill="#0b0b0b"/>
            <g fill="none" stroke="#e9bd55" stroke-width="1.1">
              <circle cx="10" cy="10" r="4.8"/>
              <ellipse cx="10" cy="10" rx="2" ry="4.8"/>
              <path d="M5.2 10h9.6"/>
            </g>
          </svg>
          www.theloombriefing.example
        </li>
      </ul>
    </div>
    <div class="tagline-band">
      <span>CORPORATE WORKWEAR</span><span class="sep">|</span>
      <span>UNIFORM SPECIALIST</span><span class="sep">|</span>
      <span>PERSONAL STYLIST</span>
    </div>
  </section>
</main>
</body>
</html>
```